Elegant Business Card for Technology Company

Client is a supplier of innovative industrial communications and automation equipment since 2002. This contest is to gather fresh ideas for a redesign of the existing business card. Client is looking for design that best communicates tagline "Industrial Networking and Computing Specialist".

Design submissions should look modern, clean, elegant and professional. It should not be cluttered. Use white as the primary colour. Orange and black as secondary colour. Refer to jpeg File 1 on the current design.

Fonts used by Client used include Arial Regular, Arial Black, Roboto Regular, Roboto Black and Lato.

The winning design will be sent for offset printing using super white 250gsm artcard paper (open for suggestions).

Target Market(s)

System Engineers, Project Managers, Purchasing Managers from companies providing engineering services for Smart Cities.

Industry/Entity Type

Information Technology

Contact Information for Business Card

Refer to PDF File 3 for Business Card Details. Priority of short contact information would be as follows Name > Job Title > Email > Mobile > Web > Tel > Fax > Business Address >UEN (UEN represents company registration number)

Font styles to use
Sans Serif

Colors
ffffff
f37122
000000
5c5c5c

Requirements
Must have
• Refer to AI File 2 (Company Logo) & PDF File 3 (Information on Namecard)
Should not have
• No QR codes
• No Social Media Icons
• Do not create full Black or Orange colour background

```html
<!DOCTYPE html>
<html lang="en">
<head>
<meta charset="utf-8">
<title>Kestrel Asia Pacific – Business Card</title>
<link rel="stylesheet" href="https://fonts.googleapis.com/css2?family=Lato:wght@400;700;900&display=swap">
<style>
  :root {
    --card: #ffffff;
    --ink: #000000;
    --orange: #f37122;
    --white: #ffffff;
    --grey: #5c5c5c;
    --backdrop: #e4e4e4;
  }
  * { margin: 0; padding: 0; box-sizing: border-box; }
  html, body { width: 1200px; height: 1189px; overflow: hidden; }
  body {
    background: var(--backdrop);
    font-family: "Lato", Arial, sans-serif;
    color: var(--ink);
    position: relative;
  }
  .card {
    position: absolute;
    left: 160px;
    width: 880px;
    height: 528px;
    background: var(--card);
    border-radius: 26px;
    overflow: hidden;
    box-shadow: 0 2px 10px rgba(0,0,0,.12);
  }
  .card--front { top: 40px; }
  .card--back { top: 620px; }

  /* brand mark */
  .brand { position: absolute; display: flex; align-items: center; gap: 14px; }
  .brand__dot { width: 58px; height: 58px; border-radius: 50%; background: var(--orange); flex: none; }
  .brand__name { font-weight: 900; font-size: 52px; letter-spacing: 1px; color: var(--ink); line-height: 1; }

  /* front */
  .card--front .brand { left: 60px; top: 150px; }
  .front__company { position: absolute; left: 136px; top: 222px; font-size: 27px; letter-spacing: .3px; color: var(--grey); }
  .front__web { position: absolute; right: 70px; top: 48px; font-size: 17px; font-weight: 700; color: var(--orange); }
  .front__rule { position: absolute; left: 60px; right: 290px; top: 300px; height: 1.5px; background: var(--orange); }
  .person { position: absolute; right: 70px; top: 252px; text-align: right; }
  .person__name { font-size: 30px; font-weight: 700; color: var(--ink); }
  .person__title { font-size: 19px; color: var(--orange); margin-top: 2px; }
  .address { position: absolute; right: 70px; top: 372px; text-align: right; font-size: 19px; line-height: 1.4; color: var(--grey); }
  .contacts { position: absolute; left: 60px; top: 330px; list-style: none; }
  .contacts li { display: flex; align-items: center; gap: 12px; font-size: 22px; line-height: 1; margin-bottom: 10px; color: var(--grey); }
  .contacts svg { width: 24px; height: 24px; flex: none; }

  /* back */
  .card--back .brand { left: 60px; top: 62px; }
  .back__company { position: absolute; right: 70px; top: 66px; font-size: 30px; letter-spacing: .3px; color: var(--grey); }
  .tagline { position: absolute; left: 60px; top: 198px; font-size: 30px; color: var(--ink); }
  .tagline-rule { position: absolute; left: 60px; right: 70px; top: 246px; border-top: 3px dotted var(--orange); }
  .services { position: absolute; left: 60px; top: 272px; list-style: none; }
  .services li { display: flex; align-items: center; gap: 22px; font-size: 27px; line-height: 1; margin-bottom: 15px; color: var(--grey); }
  .services li::before { content: ""; width: 16px; height: 16px; border-radius: 50%; background: var(--orange); flex: none; }
  .back__texture {
    position: absolute; right: 0; top: 250px; width: 440px; height: 278px;
    background: radial-gradient(ellipse at 70% 45%, rgba(0,0,0,.04), rgba(0,0,0,0) 70%);
  }
  .uen { position: absolute; right: 70px; top: 352px; font-size: 27px; color: var(--ink); }
  .uen__label { color: var(--orange); margin-right: 12px; }
</style>
</head>
<body>

<section class="card card--front" aria-label="Business card front">
  <div class="brand">
    <span class="brand__dot"></span>
    <span class="brand__name">KESTREL</span>
  </div>
  <p class="front__company">Kestrel Asia Pacific Pte Ltd</p>
  <p class="front__web">www.kestrelap.com</p>
  <div class="front__rule"></div>
  <div class="person">
    <p class="person__name">Daniel Koh</p>
    <p class="person__title">Sales Manager</p>
  </div>
  <p class="address">22 Kallang Way Harbour Tech Hub<br>#05-12 (Block B), Singapore 349207</p>
  <ul class="contacts">
    <li>
      <svg viewBox="0 0 24 24" aria-hidden="true"><rect width="24" height="24" rx="3" fill="#f37122"/><rect x="8" y="4" width="8" height="16" rx="1.5" fill="none" stroke="#ffffff" stroke-width="2"/><circle cx="12" cy="17" r="1" fill="#ffffff"/></svg>
      +65 9123 4567
    </li>
    <li>
      <svg viewBox="0 0 24 24" aria-hidden="true"><rect width="24" height="24" rx="3" fill="#f37122"/><path d="M5 9c0-2 3-3 7-3s7 1 7 3v2h-3V9.5H8V11H5z" fill="#ffffff"/><rect x="7" y="12" width="10" height="6" rx="1" fill="#ffffff"/></svg>
      +65 6345 2210
    </li>
    <li>
      <svg viewBox="0 0 24 24" aria-hidden="true"><rect width="24" height="24" rx="3" fill="#f37122"/><rect x="7" y="4" width="10" height="6" fill="none" stroke="#ffffff" stroke-width="2"/><rect x="4" y="10" width="16" height="9" rx="1" fill="#ffffff"/></svg>
      +65 6345 2219
    </li>
    <li>
      <svg viewBox="0 0 24 24" aria-hidden="true"><rect width="24" height="24" rx="3" fill="#f37122"/><rect x="4" y="7" width="16" height="11" fill="none" stroke="#ffffff" stroke-width="2"/><path d="M4 7l8 6 8-6" fill="none" stroke="#ffffff" stroke-width="2"/></svg>
      hello@kestrelap.com.sg
    </li>
  </ul>
</section>

<section class="card card--back" aria-label="Business card back">
  <div class="back__texture" role="img" aria-label="Faint dot texture decoration"></div>
  <div class="brand">
    <span class="brand__dot"></span>
    <span class="brand__name">KESTREL</span>
  </div>
  <p class="back__company">Kestrel Asia Pacific Pte Ltd</p>
  <p class="tagline">Industrial Networking and Computing Specialist</p>
  <div class="tagline-rule"></div>
  <ul class="services">
    <li>Industrial Ethernet / Wireless / Cellular</li>
    <li>Industrial and Embedded Computing</li>
    <li>Serial / Fieldbus Connectivity</li>
    <li>IP Video Surveillance</li>
    <li>Remote Automation</li>
  </ul>
  <p class="uen"><span class="uen__label">UEN No</span>20190457</p>
</section>

</body>
</html>
```